KRT Info Brochure

We need a brochure design for a new not-for-profit organisation that is aimed at providing homeless people with a residence that also provides counselling and vocational training to assist them to find suitable employment at the end of the program.
PLEASE NOTE:
Brochure to be A4.
I know the brochure is quite long, it is really a booklet, but please note that it does not have to have a lot of work done on it, I just want it to look professional and the front cover and inside page to look good.
Also please leave about 2-3 pages at the end as I will be adding in some architect drawings.
Please add in a last page with Contact written at the bottom - we will fill that in later. So please ensure it is editable in PDF.
Thank you so much.
Cheers
Marta

```html
<!DOCTYPE html>
<html lang="en">
<head>
<meta charset="utf-8">
<title>KRT Info Brochure – Inside Spread</title>
<link href="https://fonts.googleapis.com/css2?family=Arimo:wght@400;700&display=swap" rel="stylesheet">
<style>
  :root{
    --olive:#9c9a3c;
    --olive-dark:#7f7d2a;
    --gold:#f2b21c;
    --text:#4a4a4a;
    --paper:#ffffff;
    --backdrop:#e4e4e4;
  }
  *{box-sizing:border-box;margin:0;padding:0}
  html,body{width:1200px;height:847px;overflow:hidden}
  body{background:radial-gradient(circle at 50% 45%,#f2f2f2,var(--backdrop));font-family:"Arimo",Arial,sans-serif;color:var(--text)}
  .spread{position:absolute;left:100px;top:70px;width:1000px;height:707px;display:flex;box-shadow:0 10px 30px rgba(0,0,0,.25)}
  .page{position:relative;width:500px;height:707px;background:var(--paper);overflow:hidden}
  .page--left{box-shadow:inset -12px 0 18px -12px rgba(0,0,0,.18)}
  .page--right{box-shadow:inset 12px 0 18px -12px rgba(0,0,0,.18)}
  .band{position:absolute;left:0;width:500px;height:70px}
  .band--top{top:0}
  .band--bottom{bottom:0}
  .content{position:absolute;left:32px;right:32px;top:78px;font-size:8.3px;line-height:1.45}
  .page--right .content{top:62px}
  p{margin-bottom:7px}
  .section-title{color:var(--olive);font-weight:700;font-size:14px;margin:8px 0 3px}
  .bullets{list-style:none;margin:3px 0 8px}
  .bullets li{position:relative;padding-left:12px;margin-bottom:1px}
  .bullets li::before{content:"";position:absolute;left:0;top:3px;width:7px;height:7px;border-radius:50%;background:var(--gold)}
  .photo{border-radius:2px}
  .photo--study{float:right;width:150px;height:72px;margin:2px 0 6px 10px;background:linear-gradient(135deg,#d9d4cc,#b73a3a 55%,#efe9e0)}
  .photo--bench{float:right;width:195px;height:118px;margin:2px 0 6px 10px;background:linear-gradient(160deg,#4f5b32,#8c8f6c 50%,#3e4a2a)}
  .fitting{position:absolute;left:0;right:0;bottom:0;height:172px}
  .photo--carers{position:absolute;left:0;bottom:0;width:255px;height:166px;background:linear-gradient(120deg,#6d86b6,#d8c8bb 50%,#a7a1b3)}
  .fitting-list{position:absolute;left:268px;top:0;margin:0;font-size:8.3px;line-height:1.45}
  .brand{position:absolute;right:40px;bottom:80px;color:var(--olive);font-weight:400;font-size:14px;letter-spacing:.5px}
  .rule{position:absolute;left:60px;right:40px;bottom:58px;height:1px;background:var(--olive)}
</style>
</head>
<body>
<main class="spread">
  <section class="page page--left">
    <svg class="band band--top" viewBox="0 0 500 70" preserveAspectRatio="none">
      <path d="M0 0H500V18C380 36 200 58 0 44Z" fill="var(--olive)"/>
      <path d="M0 44C200 58 380 36 500 18V22C380 42 200 62 0 50Z" fill="var(--gold)"/>
    </svg>
    <div class="content">
      <p>Life skills can be thought of in terms of four broad categories:</p>
      <ul class="bullets">
        <li>Core or basic skills (eg. numeracy, literacy and information technology)</li>
        <li>Independent living skills (eg. finance, nutrition, employment)</li>
        <li>Social skills (eg. interpersonal skills, conflict resolution, developing self-confidence and social networks)</li>
        <li>Society Requirements (eg. voting, taxation etc)</li>
      </ul>
      <p>It is anticipated that most Residents will need to undertake some aspect of Life Skills, which skills are required will be assessed during the initial intake phase. Life Skills content will vary widely depending upon the individual requirement.</p>

      <h2 class="section-title">2.4. Special Needs</h2>
      <div class="photo photo--study" role="img" aria-label="Photo of a tired child resting his head on a desk over homework"></div>
      <p>According to one study, the number of homeless youth diagnosed with learning disabilities is double the rate of other children. Another study found that 28% of homeless youth have ADD. As such, KRT plans to work one on one with Residents with learning disabilities to assist them to undertake various training options with the final aim of placing them in a suitable employment situation.</p>

      <h2 class="section-title">2.5. Vocational Education</h2>
      <p>Vocational education is education that prepares people for specific trades, crafts and careers at various levels from a trade, a craft, technician, or a professional position. Residents will work closely with their Case Manager and decide on a way forward for the individual, based on their skills, abilities, likes and dislikes, attitude and aptitude. Appropriate training will be sourced to suit the Residents individual needs and a plan to help the individual Resident to reach his/her goals will be developed.</p>
      <p>KRT will do everything in its power to assist the Resident to achieve their desired outcomes, as vocational skills training is the cornerstone of Residents moving into independent living options.</p>

      <h2 class="section-title">2.6. Fitting back into Society</h2>
      <p>Once the Residents are ready to fit back into Society, KRT will assist them every step of the way. The Residents Caseworker will step them through all aspects of independent living assisting them with finding:</p>
    </div>
    <div class="fitting">
      <div class="photo photo--carers" role="img" aria-label="Photo of a young carer smiling with an elderly woman, holding hands"></div>
      <ul class="bullets fitting-list">
        <li>Appropriate Employment</li>
        <li>Housing / tenancy agreements</li>
        <li>Connecting utilities</li>
        <li>Furnishing</li>
        <li>Transportation</li>
        <li>Schools</li>
        <li>Churches</li>
        <li>Club/meeting locations</li>
      </ul>
    </div>
    <svg class="band band--bottom" viewBox="0 0 500 70" preserveAspectRatio="none">
      <path d="M255 34C350 28 430 14 500 4V8C430 20 350 34 255 40Z" fill="var(--gold)"/>
      <path d="M255 40C350 34 430 20 500 8V70H255Z" fill="var(--olive)"/>
    </svg>
  </section>

  <section class="page page--right">
    <svg class="band band--top" viewBox="0 0 500 70" preserveAspectRatio="none">
      <path d="M0 0H500V30C340 10 160 22 0 44Z" fill="var(--olive)"/>
      <path d="M0 44C160 22 340 10 500 30V34C340 16 160 28 0 50Z" fill="var(--gold)"/>
    </svg>
    <div class="content">
      <h2 class="section-title">2.7. Outreach / After Care Program</h2>
      <p>Once a Resident has finished the internal program, they will be transitioned over a period of time to become a Client. The Client will be assisted to fit back into society (see above) over a period of time to ensure that they have every chance at success.</p>
      <p>KRT will continue to support Clients once they are successfully returned to society. The Clients Case Worker will become their life coach. The Case Worker/life coach will check in on the Client on a regular basis. If the Client is struggling the Case Worker/life coach will provide whatever assistance is necessary to keep them on track. The Client will be treated as a part of the KRT family and will be invited to significant events throughout the year.</p>

      <h2 class="section-title">2.8. Family Groups</h2>
      <p>The age breakdown demonstrates a relatively even spread of homelessness between age groups, with a significant number of Under 12's contributing to the statistic. Children who are experiencing homelessness are almost always in a family group, most commonly with a single mother. Recent research has highlighted the problem of single fathers, who are often reluctant to reveal they have children for fear of losing visitation rights.</p>
      <p>Given the significance of this category, KRT will take up to 5 family groups (4 x 4, 1 x 6) at any one time in specially catered family quarters. In addition, we will also have 2 double rooms and 2 triple rooms for other family groups or couples. The entire family will be put into a program as per their individual requirements, with the aim of transitioning families as soon as possible in order to minimize impact to children and mitigating any future issues. During their time at KRT, parents will undertake the program whilst children will be enrolled at the local regional school, where possible or home schooled by suitably qualified teachers. Families will be given significant support to find appropriate housing, employment and schooling and the parent will be supported and encouraged to find employment or training.</p>

      <div class="photo photo--bench" role="img" aria-label="Photo of a homeless man sleeping on a park bench"></div>
      <h2 class="section-title">2.9. Young People</h2>
      <p>Under 24's make up a significant portion of homelessness. The program aim for young people will be to place them in on-going meaningful employment. The KRT Caseworker will work closely with the young person to assess existing skills, career aspirations and current opportunities and slowly work toward achieving employability. However, first and foremost will be the need to address the reasons and impact of homelessness.</p>
    </div>
    <div class="brand">KRT</div>
    <div class="rule"></div>
    <svg class="band band--bottom" viewBox="0 0 500 70" preserveAspectRatio="none">
      <path d="M0 70V40C140 56 320 50 500 30V70Z" fill="var(--olive)"/>
      <path d="M0 34C140 50 320 44 500 24V30C320 50 140 56 0 40Z" fill="var(--gold)"/>
    </svg>
  </section>
</main>
</body>
</html>
```